This book will apply the 12 Steps to gaming addiction, also known as video game addiction. The primary purpose of the book is to provide an effective solution for this new type of addiction. The solution is based on the rich and successful concepts of traditional twelve-step programs like RQ.

The title on the cover will be "Nine Doors Out of the Endless Level" and "by Peter Halvorn". A subtitle can be used if it works in your design of "A Practical Path Back from Compulsive Screen Play". Cover will be for a 6" x 9" book approximately 110 pages in length.

Some back cover text including some review quotes and an author bio are in the attached Word doc. There is also an author photo attached for for the back cover.

Requirements
Must have
• For the cover design it could be stylized, or an image, a partial image, or whatever. I am open to suggestions. Think about what would be noticed by a person searching for help with moderating their video game use, or by the parents or loved ones of problem gamers. Something contemporary and eye catching.

```html
<!DOCTYPE html>
<html lang="en">
<head>
<meta charset="utf-8">
<title>Nine Doors Out of the Endless Level — Full Cover</title>
<link rel="stylesheet" href="https://fonts.googleapis.com/css2?family=Anton&family=Marcellus+SC&family=Montserrat:wght@300;400&display=swap">
<style>
  :root{
    --navy:#1c212d;
    --navy-deep:#141821;
    --green:#a9c23b;
    --white:#ffffff;
    --ink:#1d2230;
  }
  *{box-sizing:border-box;margin:0;padding:0}
  html,body{width:1200px;height:1200px;overflow:hidden;background:#ffffff}
  .cover{
    position:absolute;left:0;top:165px;width:1200px;height:870px;
    background:var(--navy);overflow:hidden;
  }
  .cover-art{
    position:absolute;left:290px;top:0;width:910px;height:870px;
    background:
      radial-gradient(ellipse 420px 300px at 520px 150px, rgba(120,132,150,.55), transparent 70%),
      radial-gradient(ellipse 300px 260px at 320px 330px, rgba(70,78,92,.6), transparent 70%),
      radial-gradient(ellipse 360px 420px at 620px 560px, rgba(40,46,58,.8), transparent 75%),
      linear-gradient(160deg, #3a4150 0%, #232936 45%, #171b24 100%);
  }
  .back-title,.front-title{position:absolute;overflow:visible}
  .back-title{left:45px;top:63px;width:197px;height:189px}
  .front-title{left:725px;top:182px;width:377px;height:361px}
  .title-small{font-family:'Anton',sans-serif;font-size:52px;fill:var(--green)}
  .title-big{font-family:'Anton',sans-serif;font-size:122px;fill:var(--white)}
  .title-outline{font-family:'Anton',sans-serif;font-size:122px;fill:none;stroke:var(--green);stroke-width:2.4}
  .back-rule{position:absolute;left:143px;top:0;width:2px;height:55px;background:var(--green)}
  .blurb{
    position:absolute;left:46px;top:268px;width:195px;height:602px;
    background:var(--green);padding:12px 12px;overflow:hidden;
    font-family:'Marcellus SC',serif;font-size:9.6px;line-height:1.42;
    letter-spacing:.07em;color:var(--ink);text-align:center;
  }
  .blurb p{margin-bottom:12px}
  .praise{
    position:absolute;left:286px;top:90px;width:244px;
    font-family:'Montserrat',sans-serif;font-weight:300;color:var(--white);
  }
  .praise-head{
    font-family:'Marcellus SC',serif;font-size:12.5px;line-height:1.1;color:var(--green);
    text-align:center;letter-spacing:.04em;margin-bottom:14px;
  }
  .quote{font-size:8.4px;line-height:1.62;text-align:justify;text-align-last:center;margin-bottom:8px}
  .source{
    font-family:'Marcellus SC',serif;font-size:8.4px;line-height:1.5;color:var(--green);
    text-align:center;letter-spacing:.06em;margin-bottom:14px;
  }
  .author-photo{
    position:absolute;left:315px;top:513px;width:193px;height:170px;
    border:1.5px solid var(--white);padding:4px;
  }
  .author-photo div{
    width:100%;height:100%;
    background:linear-gradient(160deg,#6f8a55 0%,#8c7a5f 45%,#2c3040 100%);
  }
  .about-head{
    position:absolute;left:286px;top:706px;width:244px;text-align:center;
    font-family:'Marcellus SC',serif;font-size:9.5px;letter-spacing:.1em;color:var(--green);
  }
  .bio{
    position:absolute;left:286px;top:730px;width:244px;
    font-family:'Montserrat',sans-serif;font-weight:300;font-size:8.4px;line-height:1.62;
    color:var(--white);text-align:justify;text-align-last:center;
  }
  .spine{
    position:absolute;left:232px;top:437px;width:730px;height:41px;
    transform:rotate(-90deg);transform-origin:365px 20px;
    display:flex;align-items:center;gap:16px;white-space:nowrap;
  }
  .spine-title{font-family:'Anton',sans-serif;font-size:30px;color:var(--white);letter-spacing:.01em}
  .spine-title .outline{color:transparent;-webkit-text-stroke:1px var(--green)}
  .spine-bar{width:2px;height:22px;background:var(--green);transform:rotate(90deg)}
  .spine-author{font-family:'Montserrat',sans-serif;font-weight:300;font-size:25px;letter-spacing:.42em;color:var(--white)}
  .front-rule{position:absolute;left:912px;width:2px;background:var(--green)}
  .front-rule.upper{top:47px;height:125px}
  .front-rule.lower{top:562px;height:262px}
  .subtitle{
    position:absolute;left:937px;top:562px;width:205px;
    font-family:'Marcellus SC',serif;font-size:22px;line-height:1.24;letter-spacing:.1em;color:var(--green);
  }
  .front-author{
    position:absolute;top:795px;
    font-family:'Montserrat',sans-serif;font-weight:300;font-size:26px;color:var(--white);
  }
  .front-author.first{right:300px;letter-spacing:.34em}
  .front-author.last{left:930px;letter-spacing:.18em}
</style>
</head>
<body>
<main class="cover">
  <div class="cover-art" role="img" aria-label="Dark photograph of a shattering game controller with flying fragments"></div>

  <div class="back-rule"></div>
  <svg class="back-title" viewBox="0 0 377 410" preserveAspectRatio="none" aria-label="Nine Doors Out of the Endless Level">
    <text class="title-small" x="0" y="53" textLength="377" lengthAdjust="spacing">NINE DOORS</text>
    <text class="title-big" x="0" y="172" textLength="377" lengthAdjust="spacingAndGlyphs">OUT OF THE</text>
    <text class="title-outline" x="0" y="285" textLength="377" lengthAdjust="spacingAndGlyphs">ENDLESS</text>
    <text class="title-big" x="0" y="398" textLength="377" lengthAdjust="spacing">LEVEL</text>
  </svg>

  <section class="blurb">
    <p>A practical path back from the challenge of compulsive screen play (aka video game addiction) based on the rich and successful tradition of the Twelve Steps.</p>
    <p>Addiction to digital gaming is a new and troubling phenomenon that has burst upon an unprepared society with alarming speed. Many people crave the use of digital games in a strikingly similar way to any other addict. Digital games are a complex software and hardware system that have been designed to promote continued and progressive usage. This sophisticated technology clearly feeds on natural addictive tendencies.</p>
    <p>The 12 Steps are one of the most effective methods for treating addiction in human history. Originating with Recovery Quorum in 1939, the 12 Steps have since been used to treat a variety of other addictions, including drugs, sex, gambling, eating disorders, and many others. Now in this groundbreaking work the 12 Steps are applied to the complex and evolving contemporary phenomenon of digital gaming addiction.</p>
  </section>

  <section class="praise">
    <h2 class="praise-head">Praise for Nine Doors Out<br>of the Endless Level</h2>
    <p class="quote">“A must-read for anyone who is addicted to or thinks they may have a problem with digital gaming. This eloquent work will also be useful to academics and clinicians exploring potential solutions. The author recognizes the similarities between gaming addiction and other addictions, and logically applies one of the most effective known solutions for addiction - The Twelve Steps.”</p>
    <p class="source">Dale Ostrander,<br>Noted Interventionist and Keynote Speaker</p>
    <p class="quote">“If you suffer from digital gaming addiction, I strongly encourage you to use this book as your road map to get you back to the real world.”</p>
    <p class="source">Owen Brackett,<br>Founder of Feedline Review.</p>
    <p class="quote">“As a high school teacher for 24 years, husband, father, coach, and 12-Step member, I can assure you that this book will transform the life of anyone who is addicted to video games. Well written, easy to understand, and a wonderful book that will provide you with a clear road map to recovery, and this includes teenagers, a group I have been working with in the classroom for decades.”</p>
    <p class="source">Luis Ortega, Harbor Vale,<br>CA High School Teacher.</p>
  </section>

  <figure class="author-photo"><div role="img" aria-label="Portrait photograph of the author"></div></figure>
  <h3 class="about-head">About the Author</h3>
  <p class="bio">Pete Halvorn is a Technology Consultant and Writer with many years of professional coding and consulting experience. He also struggled with addiction to drugs and alcohol and is now clean and sober in a Twelve-Step program for over 17 years. This unique combination of 12-Step experience and technology expertise led him to create Nine Doors Out of the Endless Level.</p>

  <div class="spine">
    <span class="spine-title">ENDLESS <span class="outline">LEVEL</span></span>
    <span class="spine-bar"></span>
    <span class="spine-author">PETER HALVORN</span>
  </div>

  <div class="front-rule upper"></div>
  <div class="front-rule lower"></div>
  <svg class="front-title" viewBox="0 0 377 410" preserveAspectRatio="none" aria-label="Nine Doors Out of the Endless Level">
    <text class="title-small" x="0" y="53" textLength="377" lengthAdjust="spacing">NINE DOORS</text>
    <text class="title-big" x="0" y="172" textLength="377" lengthAdjust="spacingAndGlyphs">OUT OF THE</text>
    <text class="title-outline" x="0" y="285" textLength="377" lengthAdjust="spacingAndGlyphs">ENDLESS</text>
    <text class="title-big" x="0" y="398" textLength="377" lengthAdjust="spacing">LEVEL</text>
  </svg>

  <p class="subtitle">A Practical Path Back from Compulsive Screen Play</p>

  <p class="front-author first">PETER</p>
  <p class="front-author last">HALVORN</p>
</main>
</body>
</html>
```